Coastline Premier Retreats Business Card Design

Design a business card for Coastline Premier Retreats. Look at the website for colors and reference. Card should have logo, name, title, office number, mobile number, email, URL and a tagline like, "Luxury Hotel & Resort Email Marketing" (This might change).

https://www.coastlinepremierretreats.example

The rest I will leave up to your imagination.

Contact Information for Business Card

Logo, name, title, office number, mobile number, email, URL and a tagline like, "Luxury Hotel & Resort Email Marketing" (This might change).

```html
<!DOCTYPE html>
<html lang="en">
<head>
<meta charset="utf-8">
<title>Coastline Premier Retreats – Business Card</title>
<link rel="stylesheet" href="https://fonts.googleapis.com/css2?family=Open+Sans:wght@400;600;700;800&display=swap">
<style>
  :root {
    --stage: #232323;
    --card-dark: #1e1e21;
    --card-dark-sweep: #26262a;
    --orange: #f47421;
    --orange-deep: #d9601a;
    --white: #ffffff;
    --muted: #d9d9d9;
  }
  * { box-sizing: border-box; margin: 0; padding: 0; }
  html, body {
    width: 1200px; height: 780px; overflow: hidden;
    background: var(--stage);
    font-family: "Open Sans", Arial, sans-serif;
  }
  .stage {
    position: relative; width: 1200px; height: 780px;
    display: flex; align-items: center; justify-content: center; gap: 60px;
  }
  .card {
    position: relative; width: 500px; height: 286px; overflow: hidden;
    box-shadow: 0 18px 40px rgba(0,0,0,.45);
  }
  /* Front */
  .card-front { background: var(--card-dark); }
  .card-front .sweep { position: absolute; inset: 0; }
  .brand {
    position: absolute; left: 26px; top: 26px;
    display: flex; align-items: center; gap: 8px;
    color: var(--white); font-weight: 800; font-size: 15px;
    letter-spacing: .06em; text-transform: uppercase;
  }
  .brand-square { width: 10px; height: 10px; background: var(--orange); }
  .accent-bar {
    position: absolute; right: 0; top: 70px; width: 10px; height: 44px;
    background: var(--orange);
  }
  .identity {
    position: absolute; right: 28px; top: 66px; text-align: right;
  }
  .person-name { font-size: 25px; font-weight: 700; line-height: 1.1; }
  .person-name .first { color: var(--orange); }
  .person-name .last { color: var(--white); }
  .person-title { color: var(--white); font-size: 12px; margin-top: 3px; letter-spacing: .02em; }
  .tagline {
    color: var(--orange); font-size: 11.5px; line-height: 1.35; margin-top: 14px;
  }
  .contacts {
    position: absolute; right: 28px; bottom: 22px; list-style: none;
  }
  .contacts li {
    display: flex; justify-content: flex-end; align-items: center; gap: 8px;
    color: var(--muted); font-size: 11px; line-height: 1.75;
  }
  .contacts svg { width: 11px; height: 11px; flex: none; }
  /* Back */
  .card-back {
    background: var(--orange);
    display: flex; align-items: center; justify-content: center; gap: 10px;
  }
  .card-back .brand-name {
    color: var(--orange-deep); font-weight: 800; font-size: 22px;
    letter-spacing: .06em; text-transform: uppercase;
  }
  .card-back .brand-square { width: 14px; height: 14px; background: var(--orange-deep); }
</style>
</head>
<body>
<main class="stage">
  <section class="card card-front" aria-label="Business card front">
    <svg class="sweep" viewBox="0 0 500 286" preserveAspectRatio="none" aria-hidden="true">
      <defs>
        <linearGradient id="sweepFill" x1="0" y1="0" x2="1" y2="1">
          <stop offset="0" stop-color="#2a2a2e"/>
          <stop offset="1" stop-color="#1e1e21"/>
        </linearGradient>
      </defs>
      <path d="M0 286 L0 120 C60 150 110 200 150 286 Z" fill="url(#sweepFill)"/>
      <path d="M0 120 C60 150 110 200 150 286 L175 286 C140 190 80 130 0 95 Z" fill="#232327"/>
    </svg>
    <div class="brand"><span class="brand-square"></span>Coastline Premier Retreats</div>
    <div class="accent-bar"></div>
    <div class="identity">
      <h1 class="person-name"><span class="first">Marta</span> <span class="last">Velenova</span></h1>
      <p class="person-title">Managing Director</p>
      <p class="tagline">Luxury Hotel &amp;<br>Resort Email Marketing</p>
    </div>
    <ul class="contacts">
      <li>(555) 014-2758
        <svg viewBox="0 0 24 24"><path fill="#f47421" d="M6.6 10.8a15 15 0 0 0 6.6 6.6l2.2-2.2a1 1 0 0 1 1-.25 11.4 11.4 0 0 0 3.6.57 1 1 0 0 1 1 1V20a1 1 0 0 1-1 1A17 17 0 0 1 3 4a1 1 0 0 1 1-1h3.5a1 1 0 0 1 1 1c0 1.25.2 2.45.57 3.57a1 1 0 0 1-.25 1z"/></svg></li>
      <li>(555) 014-7777
        <svg viewBox="0 0 24 24"><rect x="6" y="2" width="12" height="20" rx="2" fill="none" stroke="#f47421" stroke-width="2.2"/></svg></li>
      <li>www.coastlinepremierretreats.example
        <svg viewBox="0 0 24 24"><circle cx="12" cy="12" r="9.5" fill="none" stroke="#f47421" stroke-width="2.2"/><path d="M2.5 12h19M12 2.5c3 3 3 16 0 19M12 2.5c-3 3-3 16 0 19" fill="none" stroke="#f47421" stroke-width="1.6"/></svg></li>
      <li>info@coastlinepremierretreats.example
        <svg viewBox="0 0 24 24"><rect x="2" y="5" width="20" height="14" rx="1.5" fill="#f47421"/><path d="M3 6l9 7 9-7" fill="none" stroke="#1e1e21" stroke-width="1.8"/></svg></li>
    </ul>
  </section>

  <section class="card card-back" aria-label="Business card back">
    <span class="brand-square"></span>
    <span class="brand-name">Coastline Premier Retreats</span>
  </section>
</main>
</body>
</html>
```